Velvet Lantern rebranding my business with a new business card

I have my new logo and now I need a refresher on my business cards. I really want something fun and fresh. I like black background or anything to make the color pop.
Logo
Name: Velvet Lantern
Contact Info as stated below:
Mira Pellow
555-013-4762
Logo
Name: Velvet Lantern
Mira Pellow
555-013-4762
fb.me/VelvetLanternbyMira
Instagram: @VelvetLanternbyMira

Industry/Entity Type

Business

Contact Information for Business Card

double-sided. Logo on one side. Contact info on the other.

Requirements
Must have
• Logo
• Name: Velvet Lantern
• Contact Info as stated below:
• Mira Pellow
• 555-013-4762
• fb.me/VelvetLanternbyMira
• fb.me/VelvetLanternbyMira

```html
<!DOCTYPE html>
<html lang="en">
<head>
<meta charset="utf-8">
<title>Velvet Lantern – Business Card</title>
<link href="https://fonts.googleapis.com/css2?family=Arvo:wght@400&family=Raleway:wght@400&display=swap" rel="stylesheet">
<style>
  :root {
    --backdrop: #111111;
    --card-light: #2b2b2b;
    --card-dark: #1b1b1b;
    --name-pink: #ec8cc4;
    --contact-green: #7fb77f;
    --icon-cream: #efe6c6;
    --icon-ink: #1c1c1c;
    --watermark: rgba(255, 255, 255, 0.045);
    --logo-lilac: #d9a6e4;
  }
  * { margin: 0; padding: 0; box-sizing: border-box; }
  html, body {
    width: 1200px; height: 1000px; overflow: hidden;
    background: var(--backdrop);
  }
  .canvas {
    position: relative; width: 1200px; height: 1000px;
  }
  .card {
    position: absolute; top: 357px;
    width: 500px; height: 286px;
    border-radius: 18px;
    background: radial-gradient(ellipse at 50% 45%, var(--card-light) 0%, var(--card-dark) 75%);
    box-shadow: 0 10px 30px rgba(0, 0, 0, 0.6);
    overflow: hidden;
  }
  .card--contact { left: 70px; }
  .card--logo { left: 630px; }

  .watermark {
    position: absolute; left: 0; right: 0; top: 50%;
    transform: translateY(-50%);
    text-align: center;
    font-family: 'Arvo', serif;
    font-size: 58px; letter-spacing: 3px;
    color: var(--watermark);
    white-space: nowrap;
  }

  .holder-name {
    position: absolute; left: 0; right: 0; top: 92px;
    text-align: center;
    font-family: 'Arvo', serif;
    font-size: 40px;
    color: var(--name-pink);
  }

  .contact-line {
    position: absolute;
    display: flex; align-items: center; gap: 8px;
    font-family: 'Raleway', sans-serif;
    font-size: 14px;
    color: var(--contact-green);
  }
  .contact-line--phone { left: 24px; top: 142px; }
  .contact-line--social { right: 24px; bottom: 26px; }

  .icon-dot {
    width: 16px; height: 16px; flex: none;
    border-radius: 50%;
    background: var(--icon-cream);
    display: flex; align-items: center; justify-content: center;
  }
  .icon-dot svg { width: 10px; height: 10px; }

  .brand-mark {
    position: absolute; left: 0; right: 0; top: 50%;
    transform: translateY(-50%);
    display: flex; align-items: center; justify-content: center; gap: 12px;
  }
  .brand-mark__dot {
    width: 22px; height: 22px; border-radius: 50%;
    background: var(--logo-lilac);
  }
  .brand-mark__name {
    font-family: 'Arvo', serif;
    font-size: 30px;
    color: var(--name-pink);
  }
</style>
</head>
<body>
<main class="canvas">

  <section class="card card--contact" aria-label="Contact side">
    <div class="watermark" aria-hidden="true">Velvet Lantern</div>
    <h1 class="holder-name">Mira Pellow</h1>
    <p class="contact-line contact-line--phone">
      <span class="icon-dot">
        <svg viewBox="0 0 24 24" aria-hidden="true"><path fill="#1c1c1c" d="M6.6 10.8a15.1 15.1 0 0 0 6.6 6.6l2.2-2.2a1 1 0 0 1 1-.25 11.4 11.4 0 0 0 3.6.57 1 1 0 0 1 1 1V20a1 1 0 0 1-1 1A17 17 0 0 1 3 4a1 1 0 0 1 1-1h3.5a1 1 0 0 1 1 1c0 1.25.2 2.45.57 3.6a1 1 0 0 1-.25 1z"/></svg>
      </span>
      555-013-4762
    </p>
    <p class="contact-line contact-line--social">
      <span class="icon-dot" aria-hidden="true"></span>
      VelvetLanternbyMira
    </p>
  </section>

  <section class="card card--logo" aria-label="Logo side">
    <div class="watermark" aria-hidden="true">Velvet Lantern</div>
    <div class="brand-mark">
      <span class="brand-mark__dot" aria-hidden="true"></span>
      <span class="brand-mark__name">Velvet Lantern</span>
    </div>
  </section>

</main>
</body>
</html>
```